Hardcore nerd needs to stand out in a sea of dull Defence business cards

Wombarra Devices is a new Australian consulting engineering company that turns research and theory into practical systems. No evangelistic fluff, just mathematics and physics into electronic and optical circuits for consumer products, scientific research or Defence applications.

We already have a recognised logo (provided) which is often dark blue/black on a light background but we're open to other combinations. (Us engineers tend to have limited aesthetic imagination :)

Some of our recent products have included:
* Instrumentation for electrical testing,
* Radar jammers,
* GPS antenna design,
* Satellite tracking systems,
* High power lasers

We're open to both single and double-sided designs - happy to be convinced either way.

P.S. Another group is working on the web page, so - alas - our web site is currently of no use for images/ideas...

Target Market(s)

Engineering managers,
Scientists

Contact Information for Business Card

Dr Colin Harte
R&D Engineer

colin@wombarradevices.com.au
0427 563 710

PO Box XXX (to be confirmed)
Kelsby ACT 2917
Australia

Font styles to use
Serif
Sans Serif

Colors

Designer to choose colors to be used in the design.

Requirements
Must have
• My contact details!
• I've had many (great) "bold and plain" designs submitted already, so feel free to be artistically creative :)
• Happy to take advice re fonts/colours/printability etc.
Nice to have
• I'm not sure if "lists" are more at home on a CV than a business card, but representative services include:
• Applied electromagnetics
• RF and high speed electronics
• Signal and image processing
• Electro-optical and laser systems
• Concept-to-prototype design services
• If you're considering double sided cards, then often measuring/alignment grids/rulers feature on the back of similar cards.
• e.g. https://www.veltranoptics.example/newgrouppage9.cfm?objectgroup_id=4183
• https://www.veltranoptics.example/newgrouppage9.cfm?objectgroup_ID=4185
• ..or even a "Smith chart" (google will return lots)
• Generic images to represent a capability might work - googling images associated with keyword for each of these areas might help:
• - "passive radar", "phased array", "fdtd", "vircator"
• RF and high speed electronic design
• - "smith chart", "microstrip circuits", "dimensioned drawing", "electronic schematic"
• - "dft", "iir filter"
• - "optical cavity". "laser energy level diagram"
• Background/watermarked images outlines/wireframes/schematics would probably look OK.
Should not have
• If a list of projects/services is provided, it is important not to make the client feel that this is "all" the company can do. Engineering design is a creative discipline (like graphics :)
• Please, no stock "military" snaps like planes, missiles, etc!

```html
<!DOCTYPE html>
<html lang="en">
<head>
<meta charset="utf-8">
<title>Wombarra Devices – Business Card</title>
<link href="https://fonts.googleapis.com/css2?family=Open+Sans:wght@700&family=Roboto:wght@400;700&display=swap" rel="stylesheet">
<style>
  :root {
    --navy: #232964;
    --navy-deep: #1f2558;
    --navy-soft: #3d4690;
    --ink: #2b2f6b;
    --grey: #6d6d72;
    --paper: #ffffff;
    --stage: #e6e7ec;
  }
  * { margin: 0; padding: 0; box-sizing: border-box; }
  html, body { width: 1200px; height: 913px; overflow: hidden; }
  body { background: var(--stage); position: relative; font-family: "Roboto", Arial, sans-serif; }

  .card {
    position: absolute;
    width: 560px;
    height: 320px;
    box-shadow: 0 10px 28px rgba(0,0,0,.18);
    overflow: hidden;
  }

  /* Front */
  .card--front { left: 70px; top: 90px; background: var(--navy-deep); }
  .front__glow {
    position: absolute; left: 0; top: 0; width: 100%; height: 100%;
    background: radial-gradient(circle at 28% 70%, var(--navy-soft) 0%, rgba(61,70,144,.45) 32%, rgba(31,37,88,0) 62%);
  }
  .front__brand {
    position: absolute; right: 44px; bottom: 86px;
    font-family: "Open Sans", Arial, sans-serif; font-weight: 700;
    color: var(--paper); text-align: left; line-height: 1;
  }
  .front__brand .brand__main { display: block; font-size: 40px; letter-spacing: 1px; }
  .front__brand .brand__sub { display: block; font-size: 19px; letter-spacing: 7.5px; margin-top: 6px; }

  /* Back */
  .card--back { left: 570px; top: 500px; background: var(--paper); }
  .back__logo {
    position: absolute; left: 40px; bottom: 62px;
    display: flex; align-items: center; gap: 14px;
  }
  .logo__dot { width: 52px; height: 52px; border-radius: 50%; background: var(--navy); flex: none; }
  .logo__name {
    font-family: "Open Sans", Arial, sans-serif; font-weight: 700; color: var(--navy); line-height: 1;
  }
  .logo__name .brand__main { display: block; font-size: 26px; letter-spacing: .5px; }
  .logo__name .brand__sub { display: block; font-size: 12.5px; letter-spacing: 5px; margin-top: 4px; }

  .contact {
    position: absolute; left: 300px; top: 56px;
    border-left: 1.5px solid var(--ink);
    padding-left: 16px; height: 190px;
    color: var(--grey); font-size: 13.5px; line-height: 1.3;
  }
  .contact__name { color: var(--ink); font-weight: 700; font-size: 19px; letter-spacing: .2px; }
  .contact__role { margin-bottom: 12px; }
  .contact__address { margin-bottom: 12px; }
  .contact__line { display: flex; align-items: center; gap: 7px; white-space: nowrap; }
  .contact__line svg { width: 12px; height: 12px; flex: none; fill: var(--ink); }
</style>
</head>
<body>

<section class="card card--front" aria-label="Card front">
  <div class="front__glow" role="img" aria-label="Soft blue glow where a faint emblem decoration sits"></div>
  <div class="front__brand">
    <span class="brand__main">WOMBARRA</span>
    <span class="brand__sub">DEVICES</span>
  </div>
</section>

<section class="card card--back" aria-label="Card back">
  <div class="back__logo">
    <span class="logo__dot"></span>
    <div class="logo__name">
      <span class="brand__main">WOMBARRA</span>
      <span class="brand__sub">DEVICES</span>
    </div>
  </div>

  <div class="contact">
    <div class="contact__name">DR COLIN HARTE</div>
    <div class="contact__role">R&amp;D Engineer</div>
    <div class="contact__address">PO Box XXX (to be confirmed)<br>Kelsby ACT 2917, Australia</div>
    <div class="contact__line">
      <svg viewBox="0 0 24 24"><path d="M6.6 10.8a15.1 15.1 0 0 0 6.6 6.6l2.2-2.2c.3-.3.7-.4 1-.2 1.1.4 2.3.6 3.6.6.6 0 1 .4 1 1V20c0 .6-.4 1-1 1A17 17 0 0 1 3 4c0-.6.4-1 1-1h3.5c.6 0 1 .4 1 1 0 1.3.2 2.5.6 3.6.1.3 0 .7-.2 1z"/></svg>
      0427 563 710
    </div>
    <div class="contact__line">
      <svg viewBox="0 0 24 24"><path d="M2 5h20v14H2z" opacity=".0"/><path d="M2 5h20v2l-10 6L2 7zM2 9l10 6 10-6v10H2z"/></svg>
      colin@wombarradevices.com.au
    </div>
    <div class="contact__line">
      <svg viewBox="0 0 24 24"><path d="M12 2a10 10 0 1 0 0 20 10 10 0 0 0 0-20zm0 2c.9 1.2 1.6 2.6 2 4h-4c.4-1.4 1.1-2.8 2-4zM4.3 14a8 8 0 0 1 0-4h3.4a16 16 0 0 0 0 4zm.8 2h3c.3 1.3.8 2.5 1.4 3.6A8 8 0 0 1 5.1 16zm3-8h-3a8 8 0 0 1 4.4-3.6C8.9 5.5 8.4 6.7 8.1 8zM12 20c-.9-1.2-1.6-2.6-2-4h4c-.4 1.4-1.1 2.8-2 4zm2.3-6H9.7a14 14 0 0 1 0-4h4.6a14 14 0 0 1 0 4zm.2 5.6c.6-1.1 1.1-2.3 1.4-3.6h3a8 8 0 0 1-4.4 3.6zm1.8-5.6a16 16 0 0 0 0-4h3.4a8 8 0 0 1 0 4z"/></svg>
      www.wombarradevices.com.au
    </div>
  </div>
</section>

</body>
</html>
```